High end Electrical/home automation Business Card

Need a card for a high end electrical and home automation company utilising the existing logo.
Phone
Email
Website

Like black look with raised detail. Don’t necessarily need to keep colour of logo it could be made grayscale or white etc

Target Market(s)

High end clients

Contact Information for Business Card

Brightmoor Electrical

Requirements
Must have
• Logo, phone, email, website, address

High end look
Nice to have
• Black background card
Raised font
Should not have
• Lots of colour

```html
<!DOCTYPE html>
<html lang="en">
<head>
<meta charset="utf-8">
<title>Brightmoor Electrical – Business Card</title>
<link rel="stylesheet" href="https://fonts.googleapis.com/css2?family=Archivo+Narrow:wght@400;700&family=Archivo:wght@700&display=swap">
<style>
  :root {
    --backdrop: #9b9b9b;
    --card: #161616;
    --card-edge: #0a0a0a;
    --raised: #8a8a8a;
    --raised-dim: #6d6d6d;
    --raised-soft: #5a5a5a;
  }
  * { margin: 0; padding: 0; box-sizing: border-box; }
  html, body {
    width: 1200px; height: 1050px; overflow: hidden;
    background: var(--backdrop);
  }
  .canvas {
    position: relative; width: 1200px; height: 1050px;
    display: flex; flex-direction: column; align-items: center; justify-content: center; gap: 70px;
  }
  .card {
    position: relative; width: 700px; height: 400px;
    background: var(--card);
    border: 1px solid var(--card-edge);
    box-shadow: 0 18px 40px rgba(0,0,0,0.35);
    overflow: hidden;
  }
  .raised {
    text-shadow: 0 -1px 0 rgba(255,255,255,0.12), 0 1px 1px rgba(0,0,0,0.8);
  }

  /* Front */
  .front-mark {
    position: absolute; left: 44px; top: 60px; width: 320px; height: 280px;
    display: flex; flex-direction: column; justify-content: center; gap: 18px;
  }
  .front-mark .dot {
    width: 70px; height: 70px; border-radius: 50%;
    background: var(--raised);
  }
  .front-mark .name {
    font-family: "Archivo", sans-serif; font-weight: 700;
    font-size: 44px; line-height: 1.05; color: var(--raised);
  }
  .contact {
    position: absolute; right: 40px; bottom: 34px; text-align: right;
    font-family: "Archivo Narrow", sans-serif; color: var(--raised);
  }
  .contact .person {
    font-weight: 700; font-size: 26px; letter-spacing: 0.5px; text-transform: uppercase;
  }
  .contact .role { font-size: 17px; margin-bottom: 12px; }
  .contact .address { font-size: 18px; line-height: 1.3; margin-bottom: 10px; }
  .contact .lines { list-style: none; font-size: 18px; line-height: 1.35; }
  .contact .lines li { display: flex; justify-content: flex-end; align-items: center; gap: 8px; }
  .contact .lines svg { width: 14px; height: 14px; fill: none; stroke: var(--raised); stroke-width: 1.6; }

  /* Back */
  .back {
    display: flex; flex-direction: column; align-items: center; justify-content: center; gap: 22px;
  }
  .back .dot {
    width: 90px; height: 90px; border-radius: 50%; background: var(--raised-dim);
  }
  .back .wordmark {
    font-family: "Archivo", sans-serif; font-weight: 700;
    font-size: 50px; color: var(--raised-dim);
  }
</style>
</head>
<body>
<main class="canvas">
  <section class="card front" aria-label="Card front">
    <div class="front-mark">
      <span class="dot" aria-hidden="true"></span>
      <span class="name raised">Brightmoor<br>Electrical</span>
    </div>
    <div class="contact raised">
      <p class="person">Daniel Hartley</p>
      <p class="role">President</p>
      <p class="address">Brightmoor Electrical LLC<br>4120 Larkspur Road<br>Fairview, Alaska 99512</p>
      <ul class="lines">
        <li>555-014-2278
          <svg viewBox="0 0 16 16" aria-hidden="true"><path d="M4 2l2.5 3-1.5 1.5a8 8 0 0 0 4.5 4.5L11 9.5l3 2.5-1.5 2C7 14 2 9 2 3.5z"/></svg>
        </li>
        <li>info@brightmoorelectrical.com
          <svg viewBox="0 0 16 16" aria-hidden="true"><rect x="1.5" y="3.5" width="13" height="9"/><path d="M1.5 3.5L8 9l6.5-5.5"/></svg>
        </li>
        <li>brightmoorelectrical.com
          <svg viewBox="0 0 16 16" aria-hidden="true"><circle cx="8" cy="8" r="6.5"/><path d="M1.5 8h13M8 1.5c-3 3.5-3 9.5 0 13M8 1.5c3 3.5 3 9.5 0 13"/></svg>
        </li>
      </ul>
    </div>
  </section>

  <section class="card back" aria-label="Card back">
    <span class="dot" aria-hidden="true"></span>
    <span class="wordmark raised">Brightmoor Electrical</span>
  </section>
</main>
</body>
</html>
```